Business Card for a mobile physiotherapy company

I need a layout for a business card for a mobile physiotherapy company.
Slogan is "Mobile Physiotherapy - Your Road To Recovery"
Phone number is 867-555-0142
Email VardenTherapy@postnest.ca (subject to change with website)
Website www.VardenTherapy.ca
My name and credentials: Luke Varden Luke Varden, BSc(kin), MPT, CAFCI, IMS
Information maybe included: Direct Billing, Services including Physiotherapy, IMS, acupuncture
Maybe include facebook and instagram logos
One side with the logo clean and sharp
Other side with details, try not to look too busy, keep everything concise

```html
<!DOCTYPE html>
<html lang="en">
<head>
<meta charset="utf-8">
<title>Varden Therapy – Business Card</title>
<link rel="stylesheet" href="https://fonts.googleapis.com/css2?family=Open+Sans:ital,wght@0,400;0,600;0,700;1,400&display=swap">
<style>
  :root {
    --backdrop: #3a322c;
    --card: #16181b;
    --card-edge: #0e0f11;
    --silver: #c9ccd0;
    --white: #f2f3f4;
    --blue: #3f63a3;
    --green: #1f7d62;
    --rule: #8d9096;
  }
  * { box-sizing: border-box; margin: 0; padding: 0; }
  html, body {
    width: 1200px; height: 864px; overflow: hidden;
    background: var(--backdrop);
    font-family: "Open Sans", Arial, sans-serif;
  }
  .canvas {
    width: 1200px; height: 864px;
    display: flex; flex-direction: column;
    align-items: center; justify-content: center; gap: 48px;
  }
  .card {
    position: relative;
    width: 630px; height: 360px;
    background: var(--card);
    border-radius: 4px;
    box-shadow: 0 14px 30px rgba(0,0,0,.45), 0 0 0 1px var(--card-edge);
    color: var(--white);
  }

  /* Front side */
  .card-front .social {
    position: absolute; top: 30px; right: 32px;
    display: flex; gap: 8px;
  }
  .card-front .social span {
    width: 26px; height: 26px; border-radius: 50%;
    background: var(--white);
  }
  .card-front .brand {
    position: absolute; top: 92px; left: 0; right: 0;
    display: flex; align-items: center; justify-content: center; gap: 14px;
  }
  .brand-mark {
    width: 16px; height: 16px;
    background: currentColor;
  }
  .brand-name {
    font-weight: 700; font-size: 40px; letter-spacing: 4px;
    text-transform: uppercase; line-height: 1;
  }
  .card-front .brand { color: var(--silver); }
  .card-front .tagline {
    position: absolute; top: 200px; left: 0; right: 0;
    text-align: center; font-size: 17px; font-style: italic; line-height: 1.6;
  }
  .card-front .services { font-style: normal; }

  /* Back side */
  .card-back .brand {
    position: absolute; left: 36px; top: 0; bottom: 0; width: 250px;
    display: flex; align-items: center; justify-content: center; gap: 10px;
    color: var(--blue);
  }
  .card-back .brand-name { font-size: 26px; letter-spacing: 2px; text-align: center; line-height: 1.2; }
  .card-back .brand-mark { width: 12px; height: 12px; flex: none; }
  .card-back .divider {
    position: absolute; left: 300px; top: 70px; height: 220px;
    width: 1px; background: var(--rule);
  }
  .details {
    position: absolute; left: 330px; top: 84px; right: 24px;
  }
  .person-name {
    color: var(--blue); font-weight: 700; font-size: 24px;
    text-transform: uppercase; letter-spacing: .5px; line-height: 1.15;
  }
  .credentials { color: var(--blue); font-size: 16px; }
  .billing { color: var(--green); font-size: 16px; font-weight: 600; margin-bottom: 16px; }
  .contact { list-style: none; font-size: 16px; line-height: 1.7; }
  .contact li { display: flex; align-items: center; gap: 10px; white-space: nowrap; }
  .contact svg { width: 14px; height: 14px; flex: none; fill: var(--blue); }
</style>
</head>
<body>
<main class="canvas">

  <section class="card card-front" aria-label="Card front">
    <div class="social" aria-label="Social media">
      <span></span><span></span>
    </div>
    <div class="brand">
      <span class="brand-mark"></span>
      <span class="brand-name">Varden Therapy</span>
    </div>
    <p class="tagline">
      Mobile Physiotherapy - Your Road To Recovery<br>
      <span class="services">Physiotherapy • IMS • Acupuncture</span>
    </p>
  </section>

  <section class="card card-back" aria-label="Card back">
    <div class="brand">
      <span class="brand-mark"></span>
      <span class="brand-name">Varden<br>Therapy</span>
    </div>
    <div class="divider"></div>
    <div class="details">
      <h1 class="person-name">Luke Varden</h1>
      <p class="credentials">BSc(kin), MPT, CAFCI, IMS</p>
      <p class="billing">Direct Billing</p>
      <ul class="contact">
        <li>
          <svg viewBox="0 0 16 16" aria-hidden="true"><path d="M3 1h3l1.5 4-2 1.2a9 9 0 0 0 4.3 4.3L11 8.5l4 1.5v3c0 1-1 2-2 2C6.4 15 1 9.6 1 3c0-1 1-2 2-2z"/></svg>
          867-555-0142
        </li>
        <li>
          <svg viewBox="0 0 16 16" aria-hidden="true"><path d="M1 3h14v10H1z M1 3l7 6 7-6" fill="none" stroke="#3f63a3" stroke-width="1.6"/></svg>
          VardenTherapy@postnest.ca
        </li>
        <li>
          <svg viewBox="0 0 16 16" aria-hidden="true"><circle cx="8" cy="8" r="6.5" fill="none" stroke="#3f63a3" stroke-width="1.5"/><path d="M1.5 8h13M8 1.5c-3 3.5-3 9.5 0 13M8 1.5c3 3.5 3 9.5 0 13" fill="none" stroke="#3f63a3" stroke-width="1.2"/></svg>
          www.VardenTherapy.ca
        </li>
      </ul>
    </div>
  </section>

</main>
</body>
</html>
```